Cedar Brook Stables, LLC

Equestrian business card to promote equine retirement, farm sitting, short term board. Located in Millbrook, SC.
Updates
Updated color schemes.
Contact Information for Business Card
Contact info, description of work.
Colors
0094D4
00A9DD
6FCCEA
C7EBF8
E9F6FB
59FF00
82FF00
B8FF75
E3FFCB
F4FFEA
F0912C
F2A743
F7CA91
FBE8D2
FDF5EE

```html
<!DOCTYPE html>
<html lang="en">
<head>
<meta charset="utf-8">
<title>Cedar Brook Stables, LLC — Business Card</title>
<link rel="stylesheet" href="https://fonts.googleapis.com/css2?family=Cinzel:wght@500;700&family=Cormorant+Garamond:wght@500;600;700&display=swap">
<style>
  :root {
    --backdrop: #869a98;
    --card: #f4f1ec;
    --ink: #0b0c0b;
    --band-text: #f7f5f0;
    --art-fill: #e3e2dc;
    --rule: #7d8784;
    --label: #f4f2ec;
  }
  * { margin: 0; padding: 0; box-sizing: border-box; }
  html, body {
    width: 1200px; height: 879px; overflow: hidden;
    background: var(--backdrop);
  }
  .sheet { position: relative; width: 1200px; height: 879px; }

  .card {
    position: absolute; width: 481px; height: 275px;
    background: var(--card); color: var(--ink);
  }
  .card--front-1 { left: 87px;  top: 125px; }
  .card--front-2 { left: 632px; top: 125px; }
  .card--front-3 { left: 87px;  top: 449px; }
  .card--back    { left: 632px; top: 449px; }

  .horse-art {
    position: absolute; left: 190px; width: 100px;
    background: var(--art-fill); border-radius: 4px;
  }
  .ground-rule {
    position: absolute; left: 171px; width: 140px; height: 1px;
    background: linear-gradient(90deg, transparent, var(--rule) 25%, var(--rule) 75%, transparent);
  }

  .line {
    position: absolute; left: 0; width: 100%;
    text-align: center; line-height: 1; white-space: nowrap;
  }
  .company {
    font-family: "Cinzel", serif; font-weight: 700;
    font-size: 25px; letter-spacing: 0; text-transform: uppercase;
  }
  .person {
    font-family: "Cormorant Garamond", serif; font-weight: 700;
    font-size: 26px; letter-spacing: 1.2px;
  }
  .contact {
    font-family: "Cormorant Garamond", serif; font-weight: 500;
    font-size: 19px; letter-spacing: 1.4px;
    font-variant-numeric: lining-nums;
  }

  .service-band {
    position: absolute; left: 0; top: 237px; width: 100%; height: 22px;
    background: var(--ink); color: var(--band-text);
    display: flex; align-items: center; justify-content: center; gap: 5px;
    font-family: "Cinzel", serif; font-weight: 500; font-size: 10.5px;
    letter-spacing: 0.5px; text-transform: uppercase; white-space: nowrap;
  }
  .service-band .sep { font-size: 6px; }

  .view-label {
    position: absolute; width: 481px; text-align: center; line-height: 1;
    font-family: "Cinzel", serif; font-weight: 500; font-size: 21px;
    letter-spacing: 1.5px; color: var(--label); text-transform: uppercase;
  }
  .view-label--f1 { left: 87px;  top: 414px; }
  .view-label--f2 { left: 632px; top: 414px; }
  .view-label--f3 { left: 87px;  top: 751px; }
  .view-label--bk { left: 632px; top: 751px; }
</style>
</head>
<body>
<main class="sheet">

  <section class="card card--front-1">
    <div class="horse-art" style="top:41px;height:68px" role="img" aria-label="Line drawing of a standing horse"></div>
    <div class="ground-rule" style="top:109px"></div>
    <p class="line company" style="top:116px">Cedar Brook Stables, LLC</p>
    <p class="line person" style="top:160px">Dana Whitfield</p>
    <p class="line contact" style="top:193px">Millbrook, SC / 803.555.0148</p>
    <div class="service-band"><span>Equine Retirement</span><span class="sep">◆</span><span>Farm Sitting</span><span class="sep">◆</span><span>Short Term Board</span></div>
  </section>

  <section class="card card--front-2">
    <div class="horse-art" style="top:29px;height:66px" role="img" aria-label="Line drawing of a standing horse"></div>
    <div class="ground-rule" style="top:95px"></div>
    <p class="line company" style="top:103px">Cedar Brook Stables, LLC</p>
    <p class="line person" style="top:149px">Dana Whitfield</p>
    <p class="line contact" style="top:181px">Millbrook, SC</p>
    <p class="line contact" style="top:202px">803.555.0148</p>
    <div class="service-band"><span>Equine Retirement</span><span class="sep">◆</span><span>Farm Sitting</span><span class="sep">◆</span><span>Short Term Board</span></div>
  </section>

  <section class="card card--front-3">
    <div class="horse-art" style="top:29px;height:66px" role="img" aria-label="Line drawing of a standing horse"></div>
    <div class="ground-rule" style="top:95px"></div>
    <p class="line company" style="top:103px">Cedar Brook Stables, LLC</p>
    <p class="line person" style="top:147px">Dana Whitfield</p>
    <p class="line contact" style="top:175px">803.555.0148</p>
    <p class="line contact" style="top:203px">Millbrook, SC</p>
    <div class="service-band"><span>Equine Retirement</span><span class="sep">◆</span><span>Farm Sitting</span><span class="sep">◆</span><span>Short Term Board</span></div>
  </section>

  <section class="card card--back">
    <div class="horse-art" style="top:81px;height:70px" role="img" aria-label="Line drawing of a standing horse"></div>
    <div class="ground-rule" style="top:151px"></div>
    <p class="line company" style="top:159px;font-size:26px">Cedar Brook Stables, LLC</p>
  </section>

  <p class="view-label view-label--f1">Front 01</p>
  <p class="view-label view-label--f2">Front 02</p>
  <p class="view-label view-label--f3">Front 03</p>
  <p class="view-label view-label--bk">Back</p>

</main>
</body>
</html>
```